Design a compelling Tarnwove Business Card that will drive people to my site

I want a business card that I can give to people—less to tell them who I am and more to direct them to my website. My website is a portal for Pelmor Aquatics Officials and a place for people who want to become Pelmor Aquatics Officials.
I am uploading my official company logo as well as a business card mockup that I did on my own. Please feel free to completely stray from this design.
I've included a screen recording of the homepage of my website as well.
Target Market(s)
Pelmor Aquatics Officials and people who desire to become one
Contact Information for Business Card
website url
Look and feel
Each slider illustrates characteristics of the customer's brand and the style your logo design should communicate.

```html
<!DOCTYPE html>
<html lang="en">
<head>
<meta charset="utf-8">
<title>Tarnwove Business Card</title>
<link rel="stylesheet" href="https://fonts.googleapis.com/css2?family=Montserrat:wght@400;500;700&display=swap">
<style>
  :root {
    --page-bg: #e9eaee;
    --brand-blue: #3b55a8;
    --soft-blue: #97aad8;
    --paper: #ffffff;
    --ink-light: #ffffff;
  }
  * { box-sizing: border-box; margin: 0; padding: 0; }
  html, body {
    width: 1200px; height: 912px; overflow: hidden;
    background: var(--page-bg);
    font-family: "Montserrat", sans-serif;
  }
  .sheet {
    width: 1200px; height: 912px;
    display: flex; flex-direction: column;
    align-items: center; justify-content: center;
    gap: 60px;
  }
  .card {
    position: relative;
    width: 600px; height: 343px;
    border-radius: 16px;
    overflow: hidden;
    box-shadow: 0 6px 18px rgba(30, 40, 80, 0.18);
  }

  /* Front */
  .card-front {
    background: var(--brand-blue);
    color: var(--ink-light);
  }
  .wordmark {
    display: flex; align-items: center; gap: 12px;
    font-weight: 700; letter-spacing: -1px; line-height: 1;
    white-space: nowrap;
  }
  .wordmark-dot { display: inline-block; border-radius: 50%; flex: none; }
  .card-front .wordmark {
    position: absolute; left: 0; right: 0; top: 108px;
    justify-content: center;
    font-size: 66px; color: var(--ink-light);
  }
  .card-front .wordmark-dot { width: 22px; height: 22px; background: var(--soft-blue); }
  .tagline {
    position: absolute; left: 0; right: 0; top: 236px;
    text-align: center;
    font-size: 15px; font-weight: 500; letter-spacing: 0.5px;
    white-space: nowrap;
  }

  /* Back */
  .card-back { background: var(--paper); }
  .card-back .wordmark {
    position: absolute; top: 50px; left: 40px; right: 0;
    justify-content: center;
    font-size: 60px; color: var(--brand-blue);
  }
  .card-back .wordmark-dot { width: 18px; height: 18px; background: var(--soft-blue); }

  .identity-band {
    position: absolute; left: 0; top: 186px;
    width: 298px; height: 118px;
    background: var(--soft-blue);
    color: var(--ink-light);
    display: flex; flex-direction: column;
    align-items: flex-end; justify-content: center;
    padding-right: 22px;
    white-space: nowrap;
  }
  .person-name { font-size: 24px; font-weight: 700; }
  .person-role { font-size: 16px; font-weight: 400; margin-top: 4px; }

  .contact-band {
    position: absolute; left: 310px; top: 128px;
    width: 290px; height: 132px;
    background: var(--brand-blue);
    color: var(--ink-light);
    display: flex; flex-direction: column; justify-content: center;
    gap: 10px;
    padding-left: 22px;
    list-style: none;
  }
  .contact-item {
    display: flex; align-items: center; gap: 10px;
    font-size: 16px; font-weight: 400;
    white-space: nowrap;
  }
  .contact-icon { width: 16px; height: 16px; flex: none; }
</style>
</head>
<body>
<main class="sheet">

  <section class="card card-front" aria-label="Card front">
    <div class="wordmark"><span class="wordmark-dot"></span><span>tarnwove</span></div>
    <p class="tagline">Where Pool Deck Officials Gather</p>
  </section>

  <section class="card card-back" aria-label="Card back">
    <div class="wordmark"><span class="wordmark-dot"></span><span>tarnwove</span></div>

    <div class="identity-band">
      <p class="person-name">Marcus Ellery</p>
      <p class="person-role">CEO &amp; Founder</p>
    </div>

    <ul class="contact-band">
      <li class="contact-item">
        <svg class="contact-icon" viewBox="0 0 16 16" aria-hidden="true">
          <path d="M4 1.5 6.2 4 5 5.6c.8 1.9 2.4 3.6 4.4 4.4L11 8.8l2.5 2.2-1.2 2.3c-.3.5-.9.8-1.5.6C6.5 12.6 3.4 9.5 2.1 5.2c-.2-.6.1-1.2.6-1.5Z" fill="#97aad8"/>
        </svg>
        <span>(555) 217-4403</span>
      </li>
      <li class="contact-item">
        <svg class="contact-icon" viewBox="0 0 16 16" aria-hidden="true">
          <rect x="1" y="3.5" width="14" height="9" rx="1" fill="#97aad8"/>
          <path d="M1.5 4 8 9l6.5-5" fill="none" stroke="#3b55a8" stroke-width="1.2"/>
        </svg>
        <span>marcus@tarnwove.com</span>
      </li>
      <li class="contact-item">
        <svg class="contact-icon" viewBox="0 0 16 16" aria-hidden="true">
          <g fill="none" stroke="#97aad8" stroke-width="1.2">
            <circle cx="8" cy="8" r="6.5"/>
            <ellipse cx="8" cy="8" rx="3" ry="6.5"/>
            <path d="M1.5 8h13M2.5 4.8h11M2.5 11.2h11"/>
          </g>
        </svg>
        <span>www.tarnwove.com</span>
      </li>
    </ul>
  </section>

</main>
</body>
</html>
```